The Harbourlight Aid Trust needs a graphic of their innovation approach

What we need?
- we have designed a new innovation approach (see attached). An innovation approach is the process one goes through in order to design and launch a new product or service.
- This new graphic will be used in meetings to help others understand what innovation is and how we do it. It will also be used in training sessions and be the starting point for innovation training materials we are creating
- We have created this draft graphic by copying and pasting new words over another charities innovation process
- We would like you to use your design magic and create our very own innovation process graphic. We would like it to be neat, simple, non fussy, easy to understand /read and in line with our brand colours
Attached:
1. PowerPoint:
- Slide 1: our innovation process
- Slide 2 explanation of process to bring it to life
- Slide 3&4: brand colours
- Slide 5: inspiration / examples of other processes we like the look of
2. Typeface brand guidelines
We can't wait to see what you come up with! Thank you :)
Target Market(s)
internal employees
Industry/Entity Type
Charity
Colors
Designer to choose colors to be used in the design.
Look and feel
Each slider illustrates characteristics of the customer's brand and the style your logo design should communicate.

```html
<!DOCTYPE html>
<html lang="en">
<head>
<meta charset="utf-8">
<title>Harbourlight Aid Trust – Innovation Approach</title>
<link rel="stylesheet" href="https://fonts.googleapis.com/css2?family=Montserrat:wght@600;700;800&display=swap">
<style>
  :root {
    --paper: #f7f5f0;
    --ink: #1d2327;
    --white: #ffffff;
    --discover: #0f7c8c;
    --define: #e99a0c;
    --define-text: #c27a00;
    --deliver: #c8325e;
  }
  html, body {
    margin: 0;
    padding: 0;
    width: 1200px;
    height: 708px;
    overflow: hidden;
    background: var(--paper);
  }
  .canvas {
    display: block;
    width: 1200px;
    height: 708px;
  }
  .milestone-label {
    font-family: "Montserrat", sans-serif;
    font-weight: 800;
    font-size: 24px;
    letter-spacing: 1.5px;
    fill: var(--ink);
  }
  .phase-label {
    font-family: "Montserrat", sans-serif;
    font-weight: 800;
    font-size: 22px;
    letter-spacing: 1px;
    fill: var(--white);
  }
  .step-label {
    font-family: "Montserrat", sans-serif;
    font-weight: 600;
    font-size: 26px;
    letter-spacing: 1.5px;
  }
  .step-discover { fill: var(--discover); }
  .step-define { fill: var(--define-text); }
  .step-deliver { fill: var(--deliver); }
  .leader {
    stroke: var(--ink);
    stroke-width: 2.5;
    stroke-dasharray: 10 9;
    fill: none;
  }
  .milestone-dot {
    fill: var(--white);
    stroke: var(--ink);
    stroke-width: 7;
  }
  .track { fill: none; stroke-width: 44; stroke-linecap: butt; }
  .track-discover { stroke: var(--discover); }
  .track-define { stroke: var(--define); }
  .track-deliver { stroke: var(--deliver); }
  .phase-discover .phase-disc { fill: var(--discover); }
  .phase-define .phase-disc { fill: var(--define); }
  .phase-deliver .phase-disc { fill: var(--deliver); }
</style>
</head>
<body>
<svg class="canvas" viewBox="0 0 1675 988" xmlns="http://www.w3.org/2000/svg" role="img" aria-label="Innovation approach: Discover, Define, Deliver">
  <defs>
    <path id="arc-discover" d="M328,522 A200,200 0 0 0 728,522"/>
    <path id="arc-define" d="M620.5,522 A196,196 0 0 1 1012.5,522"/>
    <path id="arc-deliver" d="M903,522 A200,200 0 0 0 1303,522"/>
  </defs>

  <rect class="backdrop" width="1675" height="988" fill="var(--paper)"/>

  <g class="track-path">
    <path class="track track-discover" d="M97,555 H384 A146,146 0 0 0 672,522" stroke-linecap="round"/>
    <path class="track track-define" d="M672,522 A144.5,144.5 0 0 1 961,522"/>
    <path class="track track-deliver" d="M961,522 A146,146 0 0 0 1245,555 H1518"/>
    <polygon class="arrow-head" fill="var(--deliver)" points="1514,513 1592,555 1514,597"/>
  </g>

  <g class="phases">
    <g class="phase phase-discover">
      <circle class="phase-disc" cx="528" cy="522" r="92"/>
      <text class="phase-label" x="528" y="530" text-anchor="middle">DISCOVER</text>
    </g>
    <g class="phase phase-define">
      <circle class="phase-disc" cx="816.5" cy="522" r="92"/>
      <text class="phase-label" x="816.5" y="530" text-anchor="middle">DEFINE</text>
    </g>
    <g class="phase phase-deliver">
      <circle class="phase-disc" cx="1103" cy="522" r="92"/>
      <text class="phase-label" x="1103" y="530" text-anchor="middle">DELIVER</text>
    </g>
  </g>

  <g class="steps">
    <text class="step-label step-discover"><textPath href="#arc-discover" startOffset="80">INSIGHT</textPath></text>
    <text class="step-label step-discover"><textPath href="#arc-discover" startOffset="425">IDEATE</textPath></text>
    <text class="step-label step-define"><textPath href="#arc-define" startOffset="52">(IN)VALIDATE</textPath></text>
    <text class="step-label step-define"><textPath href="#arc-define" startOffset="345">TEST</textPath></text>
    <text class="step-label step-deliver"><textPath href="#arc-deliver" startOffset="192">DELIVERY PLAN</textPath></text>
  </g>

  <g class="leaders">
    <line class="leader" x1="230" y1="393" x2="230" y2="522"/>
    <line class="leader" x1="528" y1="701" x2="528" y2="842"/>
    <line class="leader" x1="816.5" y1="212" x2="816.5" y2="344"/>
    <line class="leader" x1="961" y1="555" x2="961" y2="848"/>
    <line class="leader" x1="1332" y1="393" x2="1332" y2="522"/>
  </g>

  <g class="milestones">
    <circle class="milestone-dot" cx="230" cy="555" r="30"/>
    <circle class="milestone-dot" cx="528" cy="668" r="30"/>
    <circle class="milestone-dot" cx="816.5" cy="377" r="30"/>
    <circle class="milestone-dot" cx="961" cy="522" r="30"/>
    <circle class="milestone-dot" cx="1332" cy="555" r="30"/>
  </g>

  <g class="milestone-labels">
    <text class="milestone-label" x="230" y="379" text-anchor="middle">CHALLENGE</text>
    <text class="milestone-label" x="528" y="873" text-anchor="middle">OPPORTUNITY</text>
    <text class="milestone-label" x="528" y="904" text-anchor="middle">STATEMENT</text>
    <text class="milestone-label" x="816.5" y="200" text-anchor="middle">CONCEPTS</text>
    <text class="milestone-label" x="961" y="878" text-anchor="middle">SOLUTION</text>
    <text class="milestone-label" x="1332" y="379" text-anchor="middle">LAUNCH</text>
  </g>
</svg>
</body>
</html>
```